Flyer, poster, banner and social media titles designs for Community Mending Chartre

The Harbourline Charter for Community Mending provide a nationally agreed framework to guide recovery policy and practice across Australia. The Principles support recovery practitioners, governments, non-government organisations and communities to deliver effective, community-centred recovery outcomes.
The Principles have recently been refreshed through extensive consultation and we require a contemporary visual identity and design suite that will increase awareness, engagement and practical application of the Principles.
The redesign will cover:
• A4 Brochure (primary publication)
• A3 Poster
• Pull up banner
• Social Media Tiles
The new design should:
• Create a recognisable brand for the Harbourline Charter.
• Appeal to both experienced and emerging recovery practitioners.
• Reflect contemporary disaster recovery practice.
• Feel people-focused rather than government-focused.
• Support future resources such as videos, implementation guides, presentations and workshop materials.
• Remain relevant for several years without requiring a major redesign.
Target Audience
• Disaster recovery practitioners
• Government agencies
• Non-government organisations
• Community recovery workers
• Recovery managers and leaders
• Community stakeholders and volunteers
The visual identity should reflect the six Principles:
• Understanding Context
• Recognising Complexity
• Community-Centred Approaches
• Coordination
• Communication
• Capacity Building
The design should communicate:
• Recovery is centred on people and communities.
• Recovery is collaborative and involves many sectors.
• Recovery is adaptive, inclusive and evidence-informed.
• Recovery supports resilience and long-term wellbeing.
• The Principles provide practical guidance for recovery practice.
We are looking for:
• Modern and professional
• Warm and approachable
• Human-centred
• Inclusive and accessible
• Australian in context
• Visually engaging
• Suitable for print and digital use
We would like to avoid:
• Images of disaster destruction
• Emergency response imagery (fire trucks, flashing lights, etc.)
• Overly corporate or bureaucratic designs
• Designs that focus on deficits rather than recovery and growth
Consider themes such as:
• Connection and collaboration
• Communities and people
• Growth, recovery and renewal
Accessibility
Designs should:
• Meet accessibility best practice
• Use clear typography
• Achieve strong colour contrast
• Be suitable for both digital and print formats

Deliverables
1. Principles Brochure
• A4 trifold size x 2 (online and print friendly version)
• A side to include cover side, logos side and overview of principles.
• B side full details of the principles
• Graphic to highlight the 3 c’s concept (RECOVERY Context, complexity, community centred, coordinate, communicate and capacity). Currently 3 circles.
• Can be printed and distributed electronically
2. Poster
• A1 and A3 versions
• Suitable for office and workshop display
3. Pull-Up Banner - 850 mm (W) × 2000 mm (H)
• Conference and event use
• High visual impact
• Strong branding and concise messaging
4. Social Media Tiles x 3

We are providing an extension and increasing the budget following feedback from designers. We are wanting the resources to look and feel different from the existing designs, considering either a different colour palette in the designs or different motif with the leave design. Any nature based designs should consider the Australian fauna or flora. Also suggest avoiding images in the designs. The principles are not numbered or liner in the concept of how they function. Happy to answer any further questions and thank you for your suggested concepts.

Disaster recovery practitioners, Government agencies , Non-government organisations, Community recovery workers and Community stakeholders and volunteers

Disaster recovery

• Modern, warm, visually engaging, human-centred, Australian in context and different to the current design.
• Symbols for each principles
• Images of disaster destruction, Emergency response imagery, Overly corporate or bureaucratic designs, Designs that focus on deficits rather than recovery and growth, avoid too much black

```html
<!DOCTYPE html>
<html lang="en">
<head>
<meta charset="utf-8">
<title>Harbourline Charter for Community Mending – Brochure Cover</title>
<link rel="stylesheet" href="https://fonts.googleapis.com/css2?family=Lexend:wght@500;600;800&display=swap">
<style>
  :root {
    --page-bg: #e2e0dc;
    --paper: #efede6;
    --teal: #1f5566;
    --leaf-green: #5a9652;
    --band-green: #4f8c45;
    --accent-orange: #ea7a33;
    --frame-white: #f7f6f2;
  }
  html, body {
    margin: 0;
    width: 1200px;
    height: 900px;
    overflow: hidden;
    background: var(--page-bg);
  }
  .canvas {
    position: relative;
    width: 1200px;
    height: 900px;
  }
  .cover-panel {
    position: absolute;
    left: 390px;
    top: 20px;
    width: 420px;
    height: 860px;
    background: var(--paper);
    box-shadow: 0 10px 30px rgba(0,0,0,0.12);
    overflow: hidden;
  }
  .cover-art {
    position: absolute;
    inset: 0;
    width: 420px;
    height: 860px;
  }
  .cover-title {
    position: absolute;
    left: 48px;
    top: 628px;
    margin: 0;
    font-family: "Lexend", sans-serif;
    line-height: 1;
  }
  .title-kicker {
    display: block;
    font-size: 16px;
    font-weight: 600;
    color: var(--teal);
    letter-spacing: 0.01em;
  }
  .title-main {
    display: block;
    margin-top: 6px;
    font-size: 56px;
    font-weight: 500;
    color: var(--teal);
    letter-spacing: -0.01em;
  }
  .title-accent {
    display: block;
    margin-top: 0;
    font-size: 58px;
    font-weight: 800;
    color: var(--leaf-green);
    letter-spacing: 0.01em;
  }
</style>
</head>
<body>
<main class="canvas">
  <article class="cover-panel">
    <svg class="cover-art" viewBox="0 0 420 860" xmlns="http://www.w3.org/2000/svg">
      <defs>
        <linearGradient id="familyPhotoTone" x1="0" y1="0" x2="0.35" y2="1">
          <stop offset="0" stop-color="#c2b65a"/>
          <stop offset="0.18" stop-color="#8fa64c"/>
          <stop offset="0.42" stop-color="#5f8a45"/>
          <stop offset="0.58" stop-color="#4d6a7c"/>
          <stop offset="0.74" stop-color="#4f7d3e"/>
          <stop offset="1" stop-color="#3f6c30"/>
        </linearGradient>
        <linearGradient id="coastPhotoTone" x1="0" y1="0" x2="0" y2="1">
          <stop offset="0" stop-color="#9fb6c9"/>
          <stop offset="0.45" stop-color="#f3b53e"/>
          <stop offset="0.7" stop-color="#c98a4a"/>
          <stop offset="1" stop-color="#8a5a34"/>
        </linearGradient>
        <linearGradient id="groupPhotoTone" x1="0" y1="0" x2="1" y2="1">
          <stop offset="0" stop-color="#8fa45a"/>
          <stop offset="0.6" stop-color="#6b5a48"/>
          <stop offset="1" stop-color="#c47a3a"/>
        </linearGradient>
      </defs>

      <rect class="photo-family" x="0" y="0" width="420" height="530" fill="url(#familyPhotoTone)"
            role="img" aria-label="Photograph of a young family walking together in a sunlit green park"/>

      <path class="accent-wave" fill="var(--accent-orange)"
            d="M0 462 Q50 424 120 452 T262 482 Q332 522 420 478 L420 860 L0 860 Z"/>
      <path class="paper-wave" fill="var(--paper)"
            d="M0 478 Q50 444 120 470 T262 500 Q332 538 420 500 L420 860 L0 860 Z"/>

      <circle class="photo-coast" cx="150" cy="498" r="100" fill="url(#coastPhotoTone)"
              stroke="var(--frame-white)" stroke-width="6"
              role="img" aria-label="Photograph of a sunset over a coastline with sea stacks"/>
      <circle class="photo-group" cx="360" cy="428" r="56" fill="url(#groupPhotoTone)"
              stroke="var(--frame-white)" stroke-width="5"
              role="img" aria-label="Photograph of community members gathered outdoors"/>

      <g class="leaf-icon" fill="var(--leaf-green)" transform="translate(322 548)">
        <path d="M0 30 L2 8" stroke="var(--leaf-green)" stroke-width="2" fill="none" stroke-linecap="round"/>
        <path d="M2 22 C-10 18 -16 8 -14 -2 C-4 2 2 12 2 22 Z"/>
        <path d="M2 18 C10 10 22 6 28 10 C22 18 12 22 2 18 Z"/>
        <path d="M2 10 C0 0 4 -10 10 -14 C14 -6 10 4 2 10 Z"/>
      </g>

      <path class="footer-band" fill="var(--band-green)"
            d="M0 812 q17.5 -14 35 0 t35 0 t35 0 t35 0 t35 0 t35 0 t35 0 t35 0 t35 0 t35 0 t35 0 t35 0 L420 860 L0 860 Z"/>
    </svg>

    <h1 class="cover-title">
      <span class="title-kicker">Harbourline Charter For</span>
      <span class="title-main">Community</span>
      <span class="title-accent">Mending</span>
    </h1>
  </article>
</main>
</body>
</html>
```